BLUE & ORANGE BALM TOPICAL BOX + LABELS TO MATCH

Hello ! I hope you're up to helping with my designs again. I appreciate all your help.
I have two topicals needing redesign.
Box + Label , once the box is together, we can slap the labels together easy.
I have CBD version and THC version of both these balms, so well start w THC, then lay out the CBD. It should be eaay with few minor differences.
PLEASE USE only tHE SMALL BOX TEMPLATE,
Anyway, once the boxes are complete, I need to revise the label to match the boxes.
1.
ORANGE BALM :
(this box color I would like orange, like a jack-o-lantern (i uploaded our current label so you can match it)
KORVEN logo outlined in Gold (on LID)
(I uploaded a picture of what the oulined logo looks like)
THC SYMBOL
ORANGE BALM (GOLD) (on Front)
HIGHLY NUTRITIOUS POWERFUL THC RELIEF
net wt. 2 oz (56 g)
SIDE PANEL :
ORGANIC INGREDIENTS : Butyrospermum Parkii Butter (Shea Butter), Persia Gratissima (Avocado) Oil, Simmondsia chinesis (Gold Jojoba) Oil , Vitus Vinifera (Grape) Seed Oil, Arnica montana (Arnica) and Symphytum officinalis (Comfrey Leaf) macerated in Sunflower Oil, Calophyllum inophyllum (Tamanu) Oil, Nigella sativa (Black Seed) Oil, Locally Harvested Beeswax, THC CANNABIS EXTRACT, Pure Cannabigerol (CBG), Proprietary Blend of Therapeutic Essential Oils (including but not limited to : Yarrow , Celery Seed , Tea Tree , Lavender , Helichrysum, Pine Scotch, Rosemary, Geranium), Tocopherol (Vitamin E, antioxidant )
Color is a Natural Result of Chamomile Steam-Distillation and May Vary in Intensity. Consistency can also Vary. For Optimal Preservation, Keep in a Cool, Dark Place. Fatty Acids may Naturally Aggregate when Exposed to Temperature Extremes Forming Beads. To Fix This, Use a Hair Dryer to Melt them Back to a Smooth Consistency.
BACK PANEL :
WARNING: THIS PRODUCT IS FOR USE BY INDIVIDUALS 21 YEARS OF AGE OR OLDER OR BY REGISTERED QUALIFYING PATIENTS ONLY. IT IS ILLEGAL TO DRIVE A MOTOR VEHICLE WHILE UNDER THE INFLUENCE OF MARIJUANA.
(Outlined Box )::
WARNING: USE BY PREGNANT OR BREASTFEEDING WOMEN OR BY WOMEN PLANNING TO BECOME PREGNANT, MAY RESULT IN FETAL INJURY, PRETERM BIRTH, LOW BIRTHWEIGHT, OR DEVELOPMENTAL PROBLEMS FOR THE CHILD.
KEEP OUT OF REACH OF CHILDREN.
CENTRAL TOXIN RESPONSE BUREAU 1 800 555 0147
THE ACTUAL VALUE OF CANNABINOIDS MAY VARY FROM THE REPORTED VALUE BY +/- 10%
ACTIVATION TIME : 10 - 60 MINUTES
MADE IN A MARIJUANA FACILITY
PACKAGED BY
MIRABEL’S LUSH Co.
QX-R-748315
www.LUSHTARTS.info
2.
BLUE BALM
white box
KORVEN Gold out line, red w blue leaf
FRONT PANEL :
BLUE BALM (blue)
net wt. 2 oz (56 g)
Ingredients : Butyrospermum Parkii Butter (Shea Butter), Aloe Barbadensis (Aloe Vera) Leaf Extract, Coco Nucifera (Coconut) Oil, THC CANNABIS EXTRACT, Cannabis Sativa Seed Oil, Pure Cannabidol (Hemp Extract), Prunes Armeniaca (Apricot) Kernal Oil, Hydrogenated Vegetable (Soybean) Oil, Prunus Amygdalus Dulcis (Sweet Almond Oil), Vitus Vinifera (Grape) Seed Oil, Macadamia Ternifolia Seed Oil, Daucus Carota (Carrot) Seed Oil, Proprietary Blend of Therapeutic Essential Oils (including but not limited to : Lavender, Chamomile), Tocopherol (Vitamin E, antioxidant)

```html
<!DOCTYPE html>
<html lang="en">
<head>
<meta charset="utf-8">
<title>KORVEN Botanic Orange Balm – Box Dieline</title>
<link href="https://fonts.googleapis.com/css2?family=Oswald:wght@300;600;700&family=Roboto+Condensed:wght@300;400;700&family=Jost:wght@400&display=swap" rel="stylesheet">
<style>
  :root{
    --box-exterior:#f26a21;
    --box-interior:#f9dc07;
    --box-text:#ffc22f;
    --gold-light:#f3d77a;
    --gold-dark:#c9a23a;
    --brand-red:#e5262a;
    --brand-green:#138a43;
    --highlight-yellow:#f2ec1e;
    --cut-line:#1d1d1b;
    --fold-line:#8fc25a;
    --legend-ink:#1d1d1b;
  }
  html,body{margin:0;padding:0;background:#fff;overflow:hidden;}
  .canvas{width:1200px;height:502px;position:relative;overflow:hidden;background:#fff;}
  .artboard{width:2560px;height:1070px;position:absolute;left:0;top:0;transform:scale(.46875);transform-origin:0 0;}
  .dieline-art{position:absolute;left:0;top:0;}
  .die .bleed{fill:var(--die-fill);}
  .die .cut{fill:none;stroke:var(--cut-line);stroke-width:1.4;}
  .die .fold{fill:none;stroke:var(--fold-line);stroke-width:1;}
  .exterior{--die-fill:var(--box-exterior);}
  .interior{--die-fill:var(--box-interior);}

  .block{position:absolute;color:var(--box-text);font-family:"Roboto Condensed",sans-serif;}
  .wordmark{font-family:"Oswald",sans-serif;font-weight:700;color:var(--brand-red);text-align:center;letter-spacing:2px;line-height:1;white-space:nowrap;}
  .botanic{font-family:"Jost",sans-serif;color:var(--box-text);text-align:center;letter-spacing:14px;font-size:21px;line-height:1;white-space:nowrap;}
  .product-name{position:absolute;overflow:visible;}
  .product-name text{font-family:"Oswald",sans-serif;font-weight:300;font-size:66px;}
  .net-wt{font-size:12px;text-align:center;font-weight:300;white-space:nowrap;}
  .body-copy{font-weight:300;text-align:justify;font-size:12.4px;line-height:16.3px;}
  .side-copy{display:flex;flex-direction:column;gap:12px;}
  .ingredients{font-weight:300;text-align:justify;font-size:10px;line-height:11px;margin:0;}
  .care-note{font-weight:300;text-align:justify;font-size:8px;line-height:10.5px;margin:0;}
  .back-copy{text-align:center;font-size:8.4px;line-height:9.6px;}
  .back-copy .claims{font-weight:700;font-size:10px;line-height:12.8px;white-space:nowrap;}
  .back-copy p{margin:0;}
  .warning-frame{border:1.4px solid var(--box-text);padding:3px 6px;margin:6px 0 8px;font-size:8.2px;line-height:9.6px;text-align:justify;text-align-last:center;}
  .fda-note{font-weight:300;font-size:8px;line-height:9.5px;}
  .thank-you{position:absolute;left:680px;top:405px;width:140px;height:180px;transform:rotate(-90deg);transform-origin:0 0;
    font-family:"Roboto Condensed",sans-serif;font-weight:300;font-size:12.3px;line-height:14px;color:var(--box-text);text-align:center;}
  .thank-you .sign{font-family:"Oswald",sans-serif;font-size:15px;letter-spacing:1px;}

  .legend{position:absolute;font-family:"Jost",sans-serif;color:var(--legend-ink);white-space:nowrap;}
  .legend .title{font-size:17.5px;line-height:21px;}
  .legend .value{font-size:13.5px;line-height:17px;}
  .legend .note{font-size:10px;}
  .swatch{position:absolute;width:57px;height:57px;}
  .legend-mark{position:absolute;font-family:"Oswald",sans-serif;white-space:nowrap;}
</style>
</head>
<body>
<div class="canvas">
<div class="artboard">

  <svg class="dieline-art" width="2560" height="1070" viewBox="0 0 2560 1070" xmlns="http://www.w3.org/2000/svg">
    <defs>
      <g id="box-dieline" class="die">
        <g class="bleed">
          <rect x="25" y="405" width="1165" height="265"/>
          <path d="M25,405 L25,380 L65,262 L310,262 L325,410 Z"/>
          <path d="M312,420 V100 Q312,22 400,22 H540 Q625,22 625,100 V420 Z"/>
          <path d="M610,417 L612,262 L870,262 L910,380 L910,417 Z"/>
          <path d="M1185,405 L1278,420 L1278,650 L1185,672 Z"/>
          <path d="M25,657 L40,812 L295,812 L338,700 L338,657 Z"/>
          <path d="M600,657 L600,700 L635,812 L900,812 L900,657 Z"/>
          <path d="M888,657 V1000 Q888,1050 960,1050 H1130 Q1200,1050 1200,1000 V657 Z"/>
        </g>
        <g class="cut">
          <path d="M318,417 L305,278 L75,278 L40,390 L40,657"/>
          <path d="M325,417 V130 H365 V135 M575,135 V130 H612 V417"/>
          <path d="M328,130 V100 Q328,38 400,38 H540 Q610,38 610,100 V130"/>
          <path d="M625,417 L625,278 L860,278 L895,390 L900,417 H1188"/>
          <path d="M1188,417 L1265,437 L1265,640 L1188,657"/>
          <path d="M40,657 L58,797 L285,797 L322,712 L325,657"/>
          <path d="M612,657 L614,700 L652,797 L888,797 L888,657"/>
          <path d="M900,657 V945 H940 V940 M1148,940 V945 H1188 V657"/>
          <path d="M903,945 V985 Q903,1035 960,1035 H1130 Q1186,1035 1186,985 V945"/>
        </g>
        <g class="fold">
          <path d="M40,417 H1188 M40,657 H1188"/>
          <path d="M325,417 V657 M612,417 V657 M900,417 V657 M1188,417 V657"/>
          <path d="M365,133 H575 M940,943 H1148"/>
        </g>
      </g>
      <linearGradient id="gold-foil" x1="0" x2="1" y1="0" y2="0">
        <stop offset="0" stop-color="#c9a23a"/><stop offset=".45" stop-color="#f3d77a"/><stop offset="1" stop-color="#c9a23a"/>
      </linearGradient>
    </defs>

    <use href="#box-dieline" class="exterior"/>
    <use href="#box-dieline" class="interior" transform="translate(1270,0)"/>

    <g class="benefit-badges" fill="none" stroke="#ffc22f" stroke-width="2">
      <circle cx="86" cy="465" r="28" role="img" aria-label="Organic ingredients badge"/>
      <circle cx="150" cy="465" r="28" role="img" aria-label="High potency badge"/>
      <circle cx="213" cy="465" r="28" role="img" aria-label="Powerful THC relief badge"/>
      <circle cx="277" cy="465" r="28" role="img" aria-label="Natural healing badge"/>
    </g>

    <path class="compliance-mark" d="M543,430 H597 L570,476 Z" fill="#138a43" stroke="#fff" stroke-width="3" role="img" aria-label="Regulatory product symbol"/>

    <g class="legend-callout">
      <circle cx="1205" cy="213" r="37" fill="#f26a21"/>
      <circle cx="1205" cy="213" r="27" fill="none" stroke="#ffc22f" stroke-width="2" role="img" aria-label="Badge sample"/>
      <path d="M1205,213 H1255 M1245,172 L1265,192" stroke="#1d1d1b" stroke-width="1"/>
      <circle cx="1275" cy="213" r="21" fill="#f2ec1e"/>
      <path d="M1248,172 C1236,160 1226,152 1228,142 C1230,134 1242,133 1248,141 C1254,133 1266,134 1268,142 C1270,152 1260,160 1248,172 Z" fill="#f2ec1e"/>
      <rect x="957" y="268" width="58" height="57" fill="url(#gold-foil)"/>
      <circle cx="1070" cy="347" r="11" fill="#138a43"/>
      <circle cx="1070" cy="376" r="11" fill="#e5262a"/>
      <path d="M806,381 C800,376 797,373 798,369 C799,366 803,366 806,369 C809,366 813,366 814,369 C815,373 812,376 806,381 Z" fill="#ffc22f"/>
    </g>
  </svg>

  <!-- Lid panel -->
  <div class="block" style="left:325px;top:198px;width:287px;">
    <div class="wordmark" style="font-size:62px;">KORVEN</div>
  </div>
  <div class="block botanic" style="left:325px;top:269px;width:287px;">BOTANIC</div>
  <svg class="product-name" style="left:325px;top:290px;" width="287" height="70" viewBox="0 0 287 70">
    <text x="143.5" y="62" text-anchor="middle" textLength="248" lengthAdjust="spacingAndGlyphs" fill="url(#gold-foil)">ORANGE BALM</text>
  </svg>

  <!-- Front panel -->
  <div class="block" style="left:325px;top:478px;width:287px;">
    <div class="wordmark" style="font-size:62px;">KORVEN</div>
  </div>
  <div class="block botanic" style="left:325px;top:543px;width:287px;">BOTANIC</div>
  <svg class="product-name" style="left:325px;top:562px;" width="287" height="70" viewBox="0 0 287 70">
    <text x="143.5" y="62" text-anchor="middle" textLength="248" lengthAdjust="spacingAndGlyphs" fill="url(#gold-foil)">ORANGE BALM</text>
  </svg>
  <div class="block net-wt" style="left:325px;top:630px;width:287px;">net wt. 2 oz (56 g)</div>

  <!-- Left panel -->
  <div class="block body-copy" style="left:58px;top:512px;width:247px;">KORVEN ORANGE BALM is a sophisticated synergy of botanial-rich actives embraced with natural and organic oils overflowing with high-content antioxidants and phytonutrients and supercharged with THC. The intrinsic nature of this balm brings forth much needed relief and healing to the areas where you need it the most. The intelligence of this alchemized blend is characterized by its powerful, repairing and deeply soothing comforts.</div>

  <!-- Top flap thank-you note -->
  <div class="thank-you">You are truly at the heart of what we do and we are so grateful to share our passion with you. We hope our product can make a difference in your life.<br><span class="sign">KORVEN</span></div>

  <!-- Side panel -->
  <div class="block side-copy" style="left:633px;top:436px;width:246px;">
    <p class="ingredients">ORGANIC INGREDIENTS : Butyrospermum Parkii Butter (Shea Butter), Persia Gratissima (Avocado) Oil, Simmondsia chinesis (Gold Jojoba) Oil, Vitus Vinifera (Grape) Seed Oil, Arnica montana (Arnica) and Symphytum officinalis (Comfrey Leaf) macerated in Sunflower Oil, Calophyllum inophyllum (Tamanu) Oil, Nigella sativa (Black Seed) Oil, Locally Harvested Beeswax, THC CANNABIS EXTRACT, Pure Cannabigerol (CBG), Proprietary Blend of Therapeutic Essential Oils (including but not limited to : Yarrow, Celery Seed, Tea Tree, Lavender, Helichrysum, Pine Scotch, Rosemary, Geranium), Tocopherol (Vitamin E, antioxidant )</p>
    <p class="care-note">Color is a Natural result of the Phytonutrients within the Formula and May Vary in Intensity. Consistency may also Vary. For Optimal Preservation, Keep in a Cool, Dark Place. Fatty Acids may Naturally Aggregate when Exposed to Temperature Extremes Forming Beads. To Fix This, Use a Hair Dryer to Melt them Back to a Smooth Consistency. For Best Results, Apply to Skin after a warm wash. Botanical oils and Healing compounds are better able to lock into the dermis when the pores are clean, warm and open.</p>
  </div>

  <!-- Back panel -->
  <div class="block back-copy" style="left:918px;top:435px;width:252px;">
    <p class="claims">POTENT RELIEF • ULTRA HEALING • NON PSYCHOACTIVE<br>SMALL BATCH • PLANT BASED • HIGH THC FORMULA</p>
    <p style="margin-top:3px;">THIS PRODUCT IS FOR USE BY INDIVIDUALS 21 YEARS OF AGE OR OLDER OR BY REGISTERED QUALIFYING PATIENTS ONLY. IT IS ILLEGAL TO DRIVE A MOTOR VEHICLE WHILE UNDER THE INFLUENCE OF MARIJUANA. ACTIVATION TIME : 30 MINUTES.</p>
    <p style="margin-top:3px;">KEEP OUT OF REACH OF CHILDREN.<br>CENTRAL TOXIN RESPONSE BUREAU 1 800 555 0147</p>
    <div class="warning-frame">WARNING: USE BY PREGNANT OR BREASTFEEDING WOMEN OR BY WOMEN PLANNING TO BECOME PREGNANT, MAY RESULT IN FETAL INJURY, PRETERM BIRTH, LOW BIRTHWEIGHT, OR DEVELOPMENTAL PROBLEMS FOR THE CHILD.</div>
    <p>THE ACTUAL VALUE OF CANNABINOIDS MAY<br>VARY FROM THE REPORTED VALUE BY +/-10%<br>MADE IN A MARIJUANA FACILITY<br>PACKAGED BY : MIRABEL’S LUSH Co. QX-R-748315</p>
    <p class="fda-note" style="margin-top:3px;">These Statements have not been evaluated by the FDA. This product is not intended to diagnose, treat, cure, or prevent any disease or condition.</p>
  </div>

  <!-- Colour legend -->
  <div class="swatch" style="left:957px;top:28px;background:var(--box-interior);"></div>
  <div class="legend" style="left:1028px;top:30px;"><div class="title">Box interior color:</div><div class="value">CMYK: 2,11,100,0</div><div class="note">(SAME AS HONEY BOX)</div></div>
  <div class="swatch" style="left:957px;top:104px;background:var(--box-exterior);"></div>
  <div class="legend" style="left:1028px;top:113px;"><div class="title">Box exterior color:</div><div class="value">CMYK: 0,74,100,0</div></div>
  <div class="swatch" style="left:957px;top:184px;background:var(--box-text);"></div>
  <div class="legend" style="left:1028px;top:194px;"><div class="title">Box Text color:</div><div class="value">CMYK: 0,23,89,0</div></div>
  <div class="legend" style="left:1300px;top:204px;"><div class="value">CMYK: 6, 0, 97, 0</div></div>
  <div class="legend-mark" style="left:1030px;top:268px;font-size:22px;line-height:24px;color:var(--gold-dark);text-align:center;">KORVEN<br><span style="font-weight:300;">ORANGE BALM</span></div>
  <div class="legend-mark" style="left:957px;top:352px;font-size:22px;font-weight:700;color:var(--brand-red);">KORVEN</div>
  <div class="legend" style="left:1086px;top:337px;"><div class="value">CMYK: 88,24,96,11</div></div>
  <div class="legend" style="left:1086px;top:366px;"><div class="value">CMYK: 0,99,100,0</div></div>

  <div class="swatch" style="left:1650px;top:737px;width:54px;height:54px;background:var(--box-interior);"></div>
  <div class="legend" style="left:1717px;top:745px;"><div class="title">Box interior color:</div><div class="value">CMYK: 2,11,100,0</div></div>

</div>
</div>
</body>
</html>
```